New Website for World Wide Charity (KOLVAN)

We need a dynamic web design for our brand new charity organisation that will be working worldwide. We will be funded by donations so need to attract people to donate.

What We Do
We work to optimise the wellbeing of the planet, the animals and all that live within. Our slogan is Achieving Vibrational Equilibrium.

We have included a Powerpoint document which may help you understand what we need, it is just an idea for structure and style, it is not set in stone so feel free to be as creative as you like!
Updates

Designs look the same

Target Market(s)

Adults 18+ with an interest in animal, environmental. Businesses that may like to support our natural world or already support our natural world.

Number of Pages Required

3 page

Colors

Designer to choose colors to be used in the design.

Requirements
Must have
• We need the website to be easy to use and understand.

Web pages will be Home, What We Do, Who We Are, Success Stories, What You Can Do (Blog section), Seek Help, Donate, Join.
Nice to have
• Natural feel, easy to navigate, Ideally the website will look natural and organic.

Natural colours, blues, greens, sand, gold, brown, grey, silver, Orange and yellow for impact.
Should not have
• Should not have a dark coloured theme.

```html
<!DOCTYPE html>
<html lang="en">
<head>
<meta charset="utf-8">
<title>Kolvan — Help Raise World Vibration</title>
<link href="https://fonts.googleapis.com/css2?family=Fjalla+One&family=Roboto:wght@300;400;500;700&display=swap" rel="stylesheet">
<style>
:root{
  --ink:#111;
  --body-text:#666;
  --ring:#5b77ae;
  --pill:#e6dbe8;
  --pill-text:#3d3f87;
  --white:#fff;
  --rule:#d9d2de;
  --foot-text:#555;
}
*{margin:0;padding:0;box-sizing:border-box}
html,body{width:1200px;height:3032px;overflow:hidden;background:var(--white)}
body{position:relative;font-family:'Roboto',sans-serif;color:var(--ink)}
.abs{position:absolute}

/* hero */
.hero{left:0;top:0;width:1200px;height:594px;
  background:
    radial-gradient(ellipse 420px 200px at 560px 130px,#f6c070cc 0%,#e59a4a88 45%,transparent 75%),
    radial-gradient(ellipse 260px 140px at 980px 520px,#8fb3b055,transparent 70%),
    radial-gradient(ellipse 300px 160px at 320px 470px,#c8763a77,transparent 70%),
    linear-gradient(90deg,#2a2614 0%,#5a3e1e 14%,transparent 32%,transparent 68%,#4a3418 86%,#231f10 100%),
    linear-gradient(#b96a2e 0%,#d8893e 22%,#8f5a2a 50%,#5a3a1e 78%,#34250f 100%);}
.nav a{position:absolute;top:60px;color:var(--white);font-size:15.5px;text-decoration:none;letter-spacing:.2px}
.nav-line{top:82px;height:2px;background:var(--white)}
.top-links{right:190px;top:18px;display:flex;align-items:center;gap:10px;font-size:14px;font-weight:700;color:var(--white)}
.top-links span{display:flex;align-items:center;gap:6px}
.top-links .sep{width:1px;height:22px;background:#ffffff99}
.brand-mark{left:538px;top:9px;width:124px;height:124px;border-radius:50%;background:#f2eef4;border:3px solid var(--ring);display:flex;align-items:center;justify-content:center;font-size:17px;color:var(--pill-text);font-weight:500;letter-spacing:1px}
.hero-title{left:0;width:1200px;top:240px;text-align:center;font-family:'Fjalla One',sans-serif;font-size:46px;font-weight:400;color:var(--white);letter-spacing:1.4px}
.hero-sub{left:290px;width:620px;top:302px;text-align:center;font-size:15px;line-height:24px;color:var(--white);font-weight:500}
.pill{display:flex;align-items:center;justify-content:center;background:var(--pill);color:var(--pill-text);font-weight:500;font-size:16px;border-radius:22px;text-transform:uppercase;text-decoration:none}

/* category cards */
.card{top:608px;width:390px;height:343px;border-radius:36px;overflow:hidden}
.card .fill{height:100%}
.card .shade{position:absolute;left:0;right:0;bottom:0;height:150px;background:linear-gradient(transparent,#000a)}
.card h3{position:absolute;left:0;right:0;top:266px;text-align:center;color:var(--white);font-size:24px;font-weight:500;letter-spacing:1px}
.card p{position:absolute;left:0;right:0;top:304px;text-align:center;color:var(--white);font-size:13px;font-weight:700;text-decoration:underline}

/* topics */
.photo-ring{width:456px;height:456px;border-radius:50%;border:3.5px solid var(--ring);padding:14px}
.photo-ring div{width:100%;height:100%;border-radius:50%}
.topic h2{font-family:'Fjalla One',sans-serif;font-size:47px;font-weight:400;letter-spacing:2.2px;line-height:52px;color:var(--ink)}
.topic p{margin-top:24px;width:464px;font-size:15px;line-height:25.7px;color:var(--body-text);font-weight:400}
.topic .pill{margin-top:30px;width:143px;height:40px}

/* footer */
.footer-bg{left:0;top:2533px;width:1200px;height:499px;
  background:
    radial-gradient(ellipse 500px 160px at 600px 2700px,transparent,transparent),
    linear-gradient(#ffffff 0%,#efe8f3 22%,#f4e9ee 42%,#efe3ee 55%,#e3d8ec 64%,#c9c0e2 72%,#a9a2d6 80%,#7f7dc0 90%,#5b5ca8 100%);}
.footer-art{left:0;top:2830px;width:1200px;height:202px;
  background:
    radial-gradient(ellipse 150px 120px at 400px 210px,#3f8a5a99,transparent 70%),
    radial-gradient(ellipse 260px 90px at 800px 60px,#c4bde499,transparent 70%),
    radial-gradient(ellipse 240px 120px at 120px 140px,#4e4f9c88,transparent 70%),
    radial-gradient(ellipse 260px 130px at 1080px 150px,#4a4b98aa,transparent 70%),
    linear-gradient(#b9b1df00 0%,#9a93d2aa 30%,#6f6db8 65%,#4e4f9e 100%);}
.foot-col h4{font-size:18px;font-weight:500;color:#222}
.foot-col a{display:block;margin-top:11px;font-size:16px;color:var(--foot-text);text-decoration:none;line-height:19.6px}
.foot-rule{left:100px;top:2756px;width:1000px;height:1px;background:var(--rule)}
.foot-small{font-size:16px;color:#222}
</style>
</head>
<body>
<header>
  <div class="abs hero" role="img" aria-label="Log cabin in a pine forest at golden sunset, with a stream on the right"></div>
  <nav class="nav">
    <a href="#" style="left:185px">HOME</a>
    <a href="#" style="left:268px">WHAT WE DO</a>
    <a href="#" style="left:402px">WHO WE ARE</a>
    <a href="#" style="left:703px">SUCCESS STORIES</a>
    <a href="#" style="left:876px">WHAT YOU CAN DO</a>
  </nav>
  <div class="abs nav-line" style="left:182px;width:319px"></div>
  <div class="abs nav-line" style="left:698px;width:321px"></div>
  <div class="abs top-links">
    <span><svg width="14" height="13" viewBox="0 0 24 22"><path d="M12 20 3.5 11.5a5 5 0 0 1 8.5-6.5 5 5 0 0 1 8.5 6.5z" fill="none" stroke="#fff" stroke-width="2.5"/></svg>DONATE</span>
    <span class="sep"></span>
    <span><svg width="12" height="13" viewBox="0 0 12 13"><circle cx="6" cy="3.5" r="3" fill="#fff"/><path d="M0 13a6 5 0 0 1 12 0z" fill="#fff"/></svg>JOIN</span>
  </div>
  <div class="abs brand-mark">KOLVAN</div>
  <h1 class="abs hero-title">HELP RAISE WORLD VIBRATION</h1>
  <p class="abs hero-sub">Lorem ipsum dolor sit amet, consectetur adipiscing elit, sed do eiusmodr incididunt ut labore et dolore magna aliqua. Quis ipsum suspendisse ultrices</p>
  <a class="abs pill" href="#" style="left:500px;top:371px;width:200px;height:40px">Make a difference</a>
</header>

<section>
  <div class="abs card" style="left:0">
    <div class="fill" role="img" aria-label="Dense green pine forest" style="background:radial-gradient(ellipse 260px 160px at 200px 140px,#8cc08a99,transparent 70%),linear-gradient(#c9dcc6 0%,#7fae78 18%,#4f8a4e 45%,#2f6434 75%,#1f4424 100%)"></div>
    <div class="shade"></div><h3>ENVIRONMENT</h3><p>FIND OUT MORE &nbsp;»</p>
  </div>
  <div class="abs card" style="left:405px">
    <div class="fill" role="img" aria-label="Elephant, giraffe and other wild animals standing together" style="background:radial-gradient(ellipse 160px 190px at 190px 220px,#8d7b66cc,transparent 72%),radial-gradient(ellipse 90px 160px at 200px 150px,#c89a52aa,transparent 70%),linear-gradient(#eef3f8 0%,#dbe4ec 35%,#b9aa92 65%,#7a6440 100%)"></div>
    <div class="shade"></div><h3>ANIMAL</h3><p>FIND OUT MORE &nbsp;»</p>
  </div>
  <div class="abs card" style="left:810px">
    <div class="fill" role="img" aria-label="Person in a dark sweater standing in a mountain meadow" style="background:radial-gradient(ellipse 70px 150px at 195px 230px,#1e2230dd,transparent 75%),radial-gradient(ellipse 240px 90px at 260px 60px,#f1eee499,transparent 70%),linear-gradient(#d6d5dc 0%,#a7a9b4 28%,#6f806c 50%,#4d6a3e 72%,#26351f 100%)"></div>
    <div class="shade"></div><h3>HUMAN</h3><p>FIND OUT MORE &nbsp;»</p>
  </div>
</section>

<main>
  <div class="abs photo-ring" style="left:116px;top:1044px"><div role="img" aria-label="Green mountain ridge above a valley at sunset" style="background:radial-gradient(ellipse 220px 70px at 260px 70px,#f0b078cc,transparent 70%),radial-gradient(ellipse 200px 180px at 150px 300px,#5f8a3acc,transparent 70%),radial-gradient(ellipse 120px 80px at 200px 390px,#8a8680aa,transparent 70%),linear-gradient(#4a4e60 0%,#c99070 16%,#8fa0b4 28%,#5f7e4a 45%,#4a6e2c 70%,#34501e 100%)"></div></div>
  <div class="abs topic" style="left:637px;top:1100px">
    <h2>ENVIRONMENT</h2>
    <p>Lorem ipsum dolor sit amet, consectetur adipiscing elit, sdo eiusmod tempor incididunt ut labore et dolore magna aliqua. Quu suspendisse ultrices gravida. Risus commodo viverra maecenan lacus vel facilisis. Lorem ipsum dolor sit amet, consectetur adiping elit, sed do eiusmod tempor incididunt ut labore et dolore magna am suspendisse ultrices gravida. Risus commodo viverra maecenas amsan lacus vel facilisis. Lorem ipsum dolor sit amet, consectetur adipiscing elit, sdo eiusmod tempor incididunt ut labore et dolore magna aliqua.</p>
    <a class="pill" href="#">Read more</a>
  </div>

  <div class="abs topic" style="left:115px;top:1586px">
    <h2>ANIMAL</h2>
    <p>Lorem ipsum dolor sit amet, consectetur adipiscing elit, sdo eiusmod tempor incididunt ut labore et dolore magna aliqua. Quu suspendisse ultrices gravida. Risus commodo viverra maecenan lacus vel facilisis. Lorem ipsum dolor sit amet, consectetur adiping elit, sed do eiusmod tempor incididunt ut labore et dolore magna am suspendisse ultrices gravida. Risus commodo viverra maecenas amsan lacus vel facilisis. Lorem ipsum dolor sit amet, consectetur adipiscing elit, sdo eiusmod tempor incididunt ut labore et dolore magna aliqua.</p>
    <a class="pill" href="#">Read more</a>
  </div>
  <div class="abs photo-ring" style="left:644px;top:1529px"><div role="img" aria-label="Brown bear with two cubs in tall grass" style="background:radial-gradient(ellipse 140px 190px at 250px 220px,#7a5a3cee,transparent 72%),radial-gradient(ellipse 110px 90px at 170px 330px,#8a6644dd,transparent 72%),linear-gradient(#93a15a 0%,#6f8040 40%,#5a6a30 75%,#4a5a26 100%)"></div></div>

  <div class="abs photo-ring" style="left:116px;top:2005px"><div role="img" aria-label="Family of four running along a country path in autumn" style="background:radial-gradient(ellipse 160px 150px at 210px 200px,#6a4a3a99,transparent 72%),radial-gradient(ellipse 70px 140px at 300px 360px,#c9b08acc,transparent 70%),linear-gradient(#9b7a52 0%,#c09a62 22%,#8a7a48 45%,#6f8a44 68%,#55733a 100%)"></div></div>
  <div class="abs topic" style="left:637px;top:2061px">
    <h2>HUMAN</h2>
    <p>Lorem ipsum dolor sit amet, consectetur adipiscing elit, sdo eiusmod tempor incididunt ut labore et dolore magna aliqua. Quu suspendisse ultrices gravida. Risus commodo viverra maecenan lacus vel facilisis. Lorem ipsum dolor sit amet, consectetur adiping elit, sed do eiusmod tempor incididunt ut labore et dolore magna am suspendisse ultrices gravida. Risus commodo viverra maecenas amsan lacus vel facilisis. Lorem ipsum dolor sit amet, consectetur adipiscing elit, sdo eiusmod tempor incididunt ut labore et dolore magna aliqua.</p>
    <a class="pill" href="#">Read more</a>
  </div>
</main>

<footer>
  <div class="abs footer-bg"></div>
  <div class="abs footer-art" role="img" aria-label="Purple mountains and pine forest with a figure standing arms open"></div>
  <div class="abs foot-col" style="left:100px;top:2591px"><h4>GET INVOLVED</h4><a href="#">Join Us</a><a href="#">Fundraise</a><a href="#">Donate</a><a href="#">Shop</a></div>
  <div class="abs foot-col" style="left:382px;top:2591px"><h4>GET HELP</h4><a href="#">Contact Us</a><a href="#">Media</a></div>
  <div class="abs foot-col" style="left:621px;top:2591px"><h4>LEGAL</h4><a href="#">Terms and Conditions</a><a href="#">Cookies</a><a href="#">Privacy Policy</a></div>
  <div class="abs brand-mark" style="left:940px;top:2567px;width:150px;height:150px;font-size:20px">KOLVAN</div>
  <div class="abs foot-rule"></div>
  <p class="abs foot-small" style="left:95px;top:2772px">Charity Number : 888 888 888</p>
  <p class="abs foot-small" style="right:97px;top:2785px;font-size:15px">© 2021 Kolvan. All Rights Reserved.</p>
</footer>
</body>
</html>
```